Organic Coconut oil

A label for a 500ml jar of organic coconut oil
The product is raw cold pressed virgin coconut oil
Target Market(s)
All health conscious individuals
Industry/Entity Type
Product
Requirements
Must have
- Virgin
Raw
Cold pressed
Organic
Product name tiko coconut oil

```html
<!DOCTYPE html>
<html lang="en">
<head>
<meta charset="utf-8">
<title>Tiko Coconut Oil – Jar Label</title>
<link rel="stylesheet" href="https://fonts.googleapis.com/css2?family=Oswald:wght@500&family=Cabin+Sketch:wght@700&family=Roboto+Slab:wght@800&display=swap">
<style>
  :root {
    --page-bg: #ffffff;
    --husk-dark: #4a2a16;
    --husk-mid: #7a4a2a;
    --husk-light: #9a6440;
    --label-ink: #ffffff;
    --shadow: rgba(0, 0, 0, 0.28);
  }
  html, body {
    margin: 0;
    padding: 0;
    width: 1200px;
    height: 854px;
    overflow: hidden;
    background: var(--page-bg);
  }
  .canvas {
    position: relative;
    width: 1200px;
    height: 854px;
  }
  .label {
    position: absolute;
    left: 0;
    top: 0;
    width: 1200px;
    height: 854px;
  }
  .label__claims {
    font-family: "Oswald", "Arial Narrow", sans-serif;
    font-weight: 500;
    font-size: 27px;
    fill: var(--label-ink);
    letter-spacing: 0.5px;
  }
  .label__brand,
  .label__product {
    font-family: "Cabin Sketch", "Comic Sans MS", cursive;
    font-weight: 700;
    fill: var(--label-ink);
  }
  .label__brand { font-size: 70px; letter-spacing: 2px; }
  .label__product { font-size: 62px; }
  .label__volume {
    font-family: "Roboto Slab", Georgia, serif;
    font-weight: 800;
    font-size: 17px;
    fill: var(--label-ink);
  }
</style>
</head>
<body>
<main class="canvas">
  <svg class="label" viewBox="0 0 1200 854" xmlns="http://www.w3.org/2000/svg">
    <defs>
      <radialGradient id="husk-fill" cx="45%" cy="40%" r="70%">
        <stop offset="0%" stop-color="var(--husk-light)"/>
        <stop offset="55%" stop-color="var(--husk-mid)"/>
        <stop offset="100%" stop-color="var(--husk-dark)"/>
      </radialGradient>
      <filter id="drop" x="-20%" y="-20%" width="140%" height="150%">
        <feGaussianBlur stdDeviation="9"/>
      </filter>
      <path id="claims-arc" d="M 482 364 A 360 360 0 0 1 914 364"/>
    </defs>

    <ellipse class="label__shadow" cx="702" cy="410" rx="236" ry="146" fill="var(--shadow)" filter="url(#drop)"/>
    <ellipse class="label__surface" cx="698" cy="396" rx="241" ry="150" fill="url(#husk-fill)"
             role="img" aria-label="Close-up photograph of brown coconut husk fibres"/>

    <text class="label__claims">
      <textPath href="#claims-arc" startOffset="50%" text-anchor="middle">VIRGIN, RAW, COLD PRESSED, ORGANIC</textPath>
    </text>
    <text class="label__brand" x="698" y="376" text-anchor="middle">TIKO</text>
    <text class="label__product" x="698" y="459" text-anchor="middle" textLength="378" lengthAdjust="spacingAndGlyphs">COCONUT OIL</text>
    <text class="label__volume" x="698" y="524" text-anchor="middle">500ml</text>
  </svg>
</main>
</body>
</html>
```